Event Website for the Audio & Visual Industry

Convene is an exhibition aimed at meeting the business needs of audio and visual professionals – the visitors are the ones that make purchase decisions when buying anything to do with AV installation, Lighting & Entertainment Technology, DJ Technologies and even Musical Instruments.

We need to rebuild our website to reflect the professional look but with a bit of creativity/flare that is associated with the industry.

Websites whose design is along the lines we're looking for:

• http:www.pelmora.com.au
• http:www.kavrin.com
• http://www.brightpanelfair.net/ (competitor expo, like the layout. Not fantastic though, but the best I’ve seen from the industry)
• http://www.tuvelo.com.au and http://www.ostrand.com.au/ (Like these brand websites, they are clean and corporate but the use of imagery allows it to have some personality)

Target Market(s)

Corporate AV End Users, Lighting Designers, Concert/Entertainment companies, Sound Engineers

Industry/Entity Type

Business

Requirements
Must have
• Refer to the current splash page – www.convene-expo.com
This is the look and feel we have developed for our brochure. We want to expand on this and create a professional corporate look and feel without alienating existing sound, light and vision sectors.

The website's focus is to register visitors to attend the show. Please include a floating 'Register Free' Call to action. Please also include floating social media buttons. For what I mean by 'floating' check out the Social media buttons on this website: http://quorvix.com/2012/02/19/tall-boat-preview/ (scroll down to see effect).

We'll like to include a Rotating Banner at the top.

Sponsor element at the bottom off the page.

Sign up form functionality

Menu to be: About the Show, What's On, Register, How to Exhibit, Blog, Contact us.

I would like to see designs for a content page as well as the homepage.

```html
<!DOCTYPE html>
<html lang="en">
<head>
<meta charset="utf-8">
<title>Convene 2012 – Sound, Light, Vision</title>
<link rel="stylesheet" href="https://fonts.googleapis.com/css2?family=Bree+Serif&family=Oxygen:wght@300;400;700&family=Arimo:wght@400;700&display=swap">
<style>
:root{
  --red:#c8141e;
  --red-dark:#9c0d16;
  --accent:#e8123c;
  --ink:#1d1d1d;
  --muted:#444;
  --black:#000;
  --bar:#1f1f1f;
  --line:#9fc3cf;
  --sky-top:#8fc4e6;
  --sky-bottom:#f4f9fc;
  --white:#fff;
  --cyan:#38b4e8;
}
*{box-sizing:border-box;margin:0;padding:0}
html,body{width:1084px;height:1200px;overflow:hidden}
body{position:relative;font-family:"Arimo",Arial,sans-serif;color:var(--ink);
  background:linear-gradient(180deg,var(--sky-top) 0,#bcdcef 180px,var(--sky-bottom) 460px,var(--white) 520px)}
.abs{position:absolute}
.topbar{left:0;top:0;width:1084px;height:26px;background:linear-gradient(#2c2c2c,#111)}
.toplinks{right:110px;top:7px;font:400 10.5px "Oxygen",sans-serif;color:#eee;word-spacing:1px}
.toplinks span{margin:0 5px;color:#999}
.logo-card{left:99px;top:0;width:181px;height:107px;background:linear-gradient(#fff,#e9e9e9);
  border-radius:0 0 8px 8px;box-shadow:0 3px 8px rgba(0,0,0,.35);display:flex;align-items:center;justify-content:center;gap:7px}
.brand{font:400 31px "Oxygen",sans-serif;color:#222;letter-spacing:-.5px}
.brand-dot{width:10px;height:10px;border-radius:50%;background:var(--red)}
.show-date{right:106px;top:42px;text-align:left}
.show-date h2{font:400 21px "Bree Serif",serif;color:#111;letter-spacing:.3px}
.show-date p{font:400 13px/16px "Oxygen",sans-serif;color:#111}
.mainnav{left:99px;top:118px;width:885px;height:33px;background:linear-gradient(#d9232b,var(--red-dark));
  border-radius:3px;box-shadow:0 1px 3px rgba(0,0,0,.4)}
.mainnav a{position:absolute;top:9px;font:400 12.5px "Oxygen",sans-serif;color:#fff;text-decoration:none}
.mainnav a.current{top:5px;left:8px;background:#fff;color:#111;padding:3px 4px;border:1px solid #999;border-radius:2px}
.newsletter{right:14px;top:7px;display:flex;align-items:center;gap:8px;font:700 11px "Oxygen",sans-serif;color:#fff}
.newsletter i{width:20px;height:19px;background:#333;border-radius:2px;display:block;position:relative}
.newsletter i:after{content:"»";position:absolute;left:6px;top:1px;font-style:normal;transform:rotate(90deg);font-size:11px}
.banner{left:99px;top:158px;width:887px;height:312px;border-radius:9px;border:2px solid #fff;overflow:hidden;
  box-shadow:0 0 0 1px #bbb,0 12px 18px -10px rgba(0,0,0,.45)}
.banner-photo{width:100%;height:100%;background:linear-gradient(180deg,#dfe9f0 0,#f4e8d8 35%,#c89a52 60%,#3a2818 78%,#1a140e 100%)}
.banner-logo{left:2px;top:48px;width:252px;height:145px;background:var(--black);display:flex;align-items:center;justify-content:center;gap:8px}
.banner-logo .brand{color:#fff;font-size:40px}
.banner-logo small{position:absolute;right:50px;bottom:4px;font:400 6px "Arimo",sans-serif;color:#ccc}
.register-cta{right:0;bottom:0;width:164px;height:96px;background:rgba(20,20,20,.85);text-align:center;padding-top:18px}
.register-cta .lead{font:700 13px "Arimo",sans-serif;color:var(--cyan);border-top:1px solid #555;padding-top:8px;margin:0 8px}
.register-cta .big{font:400 19px "Oxygen",sans-serif;color:#fff;border-bottom:1px solid #777;padding-bottom:4px;margin:0 8px}
.social-tab{left:987px;top:235px;width:41px;height:160px;background:linear-gradient(90deg,var(--red-dark),var(--red));border-radius:0 8px 8px 0;
  padding:15px 0 0 5px;display:flex;flex-direction:column;gap:9px}
.social-tab span{width:27px;height:27px;border-radius:4px;background:linear-gradient(#f4f4f4,#c9c9c9);display:block}
.content{left:98px;top:494px;width:888px;height:500px;background:var(--white);border:1px solid var(--line);border-bottom:0}
.gallery-arrow{top:41px;width:27px;height:54px;background:linear-gradient(90deg,#f5f5f5,#e9e9e9)}
.thumb{top:27px;width:97px;height:83px;border:1px solid #777;box-shadow:0 10px 8px -8px rgba(0,0,0,.25)}
.info-box{top:150px;height:148px;border:1px solid var(--line);padding:10px 14px}
.info-box h3{font:400 13.5px/18px "Oxygen",sans-serif;color:#111}
.info-box h3 em{font-style:normal;color:var(--accent)}
.info-box .pic{margin:8px 0 0 8px;width:197px;height:61px;border-radius:3px}
.info-box ul{list-style:none;font:400 10px/16.3px "Arimo",sans-serif;color:#111;margin-top:10px}
.action-box{top:329px;height:129px;background:linear-gradient(#fff,#ececec);border:1px solid #e2e2e2}
.action-box h3{font:400 16px "Oxygen",sans-serif;color:#111;margin:10px 0 0 11px;letter-spacing:-.3px}
.action-box h3 em{font-style:normal;color:var(--accent)}
.action-box p{font:400 12px/15px "Arimo",sans-serif;color:#111;margin:12px 0 0 8px;letter-spacing:-.2px}
.action-bar{position:absolute;left:0;bottom:0;width:100%;height:32px;background:linear-gradient(#2a2a2a,#0c0c0c);
  display:flex;align-items:center;gap:6px;padding-left:10px;font:400 16px "Oxygen",sans-serif;color:#fff}
.action-bar i{width:12px;height:12px;border-radius:50%;background:var(--accent);position:relative}
.action-bar i:after{content:"";position:absolute;left:4px;top:3px;border:3px solid transparent;border-left:4px solid #fff}
.footer{left:0;top:983px;width:1084px;height:169px;background:var(--black)}
.footer-nav{left:129px;top:12px;list-style:none;font:300 13px/22px "Oxygen",sans-serif;color:#ddd}
.footer-rule{top:18px;width:1px;height:141px;background:#444}
.footer-note{left:258px;top:17px;width:420px;font:400 11px/16px "Arimo",sans-serif;color:#fff;letter-spacing:-.2px}
.follow{left:259px;top:117px;font:300 13px "Oxygen",sans-serif;color:#ccc}
.follow-icons{left:259px;top:121px;display:flex;gap:7px}
.follow-icons span{width:25px;height:25px;background:#555;border-radius:3px}
.partner{left:786px;top:57px;width:165px;height:72px;background:#fff;padding:6px 12px}
.partner small{font:italic 400 10px "Arimo",sans-serif;color:#111}
.partner .plate{margin-top:6px;width:140px;height:38px;background:#e6e6e6}
.copyright{left:113px;top:1172px;font:400 11.5px "Arimo",sans-serif;color:#111;letter-spacing:-.3px}
.organiser{left:866px;top:1165px;font:700 16px "Arimo",sans-serif;color:#111;display:flex;align-items:center;gap:5px}
.organiser i{width:8px;height:8px;background:var(--red);display:block}
</style>
</head>
<body>
<header>
  <div class="abs topbar"></div>
  <nav class="abs toplinks">Your wishlist<span>|</span>Your Account<span>|</span>Register Your Product</nav>
  <div class="abs logo-card"><span class="brand">convene</span><span class="brand-dot"></span></div>
  <div class="abs show-date">
    <h2>21st - 23rd AUGUST 2012</h2>
    <p>Harbourside Exhibition Hall,<br>Wattle Quay, Australia</p>
  </div>
  <nav class="abs mainnav">
    <a class="current" href="#">About the Show</a>
    <a href="#" style="left:146px">What's On</a>
    <a href="#" style="left:250px">Register</a>
    <a href="#" style="left:341px">How to Exhibition</a>
    <a href="#" style="left:484px">Blog</a>
    <a href="#" style="left:556px">Contact Us</a>
    <div class="abs newsletter">NEWSLETTER <i></i></div>
  </nav>
</header>

<section class="abs banner">
  <div class="banner-photo" role="img" aria-label="Harbour bridge and opera house lit at dusk"></div>
  <div class="abs banner-logo"><span class="brand">convene</span><span class="brand-dot"></span><small>in association with</small></div>
  <a class="abs register-cta" href="#"><div class="lead">Click here to</div><div class="big">REGISTER NOW</div></a>
</section>

<aside class="abs social-tab" aria-label="Social links"><span></span><span></span><span></span><span></span></aside>

<main class="abs content">
  <div class="abs gallery-arrow" style="left:15px"><svg width="27" height="54"><path d="M17 20l-7 7 7 7" stroke="#bbb" stroke-width="2.5" fill="none"/></svg></div>
  <div class="abs gallery-arrow" style="left:848px"><svg width="27" height="54"><path d="M10 20l7 7-7 7" stroke="#bbb" stroke-width="2.5" fill="none"/></svg></div>
  <div class="abs thumb" style="left:48px;background:linear-gradient(135deg,#2c1e44,#7a5fb0,#2a2440)" role="img" aria-label="Mixing desk"></div>
  <div class="abs thumb" style="left:164px;background:linear-gradient(135deg,#111,#6a7b96,#1a1a1a)" role="img" aria-label="Display wall"></div>
  <div class="abs thumb" style="left:274px;background:linear-gradient(180deg,#6d7c96,#2f2a3e)" role="img" aria-label="Stage lighting rig"></div>
  <div class="abs thumb" style="left:390px;background:linear-gradient(135deg,#aaa,#333,#666)" role="img" aria-label="Lighting fixtures"></div>
  <div class="abs thumb" style="left:505px;background:linear-gradient(180deg,#c8c0b0,#4b4036)" role="img" aria-label="Exhibition hall crowd"></div>
  <div class="abs thumb" style="left:622px;background:linear-gradient(135deg,#3a5aa8,#c8d4ee,#2a3a70)" role="img" aria-label="Control console"></div>
  <div class="abs thumb" style="left:739px;background:linear-gradient(180deg,#6a7894,#3a2e44)" role="img" aria-label="Stage lighting rig"></div>

  <div class="abs info-box" style="left:15px;width:276px">
    <h3>AUSTRALIA'S Largest Audio Visual <em>Entertainment</em> &amp; Information Communications <em>Technology</em> Event</h3>
    <div class="pic" style="background:linear-gradient(90deg,#102060,#4a7ad0,#182a6a)" role="img" aria-label="Lit stage truss"></div>
  </div>
  <div class="abs info-box" style="left:307px;width:276px">
    <h3 style="margin-left:11px">Be Part of Australia's Only Event for the Audio Visual &amp; <em>Entertainment</em> Industry</h3>
    <div class="pic" style="margin-left:24px;background:linear-gradient(90deg,#06122e,#3a6ac0,#0a1430)" role="img" aria-label="Concert crowd and stage"></div>
  </div>
  <div class="abs info-box" style="left:598px;width:276px">
    <h3>DISCOVER THE LATEST <em>ADVANCEMENTS</em> IN...</h3>
    <ul><li>• Concert Production • AV Installation • Broadcast • Staging • Lighting &amp; Entertainment Technology • Digital Media &amp; Information Services • Education Technology • Post Production • Multimedia • Audio Engineering • Recording • DJ Technologies • Musical Instruments</li></ul>
  </div>

  <div class="abs action-box" style="left:15px;width:424px">
    <h3>CONTACT THE <em>CONVENE TEAM</em></h3>
    <p>Lorem ipsum dolor sit amet, consectetur adipiscing elit. Nullam semper accumsan mi quis elementum. Curabitur suscipit tristique dapibus</p>
    <a class="action-bar" href="#"><i></i>Click Here</a>
  </div>
  <div class="abs action-box" style="left:451px;width:433px">
    <h3>DOWNLOAD THE <em>FLOOR PLAN</em></h3>
    <p style="font-size:11px">Lorem ipsum dolor sit amet, consectetur adipiscing elit. Nullam<br>semper accumsan mi quis elementum. Curabitur suscipit</p>
    <a class="action-bar" href="#"><i></i>DOWNLOAD</a>
  </div>
</main>

<footer class="abs footer">
  <ul class="abs footer-nav"><li>Home</li><li>About The Show</li><li>What's On</li><li>Register</li><li>How to Exhibit</li><li>Blog</li><li>Contact Us</li></ul>
  <div class="abs footer-rule" style="left:239px"></div>
  <div class="abs footer-rule" style="left:746px"></div>
  <div class="abs footer-note">STRICTLY TRADE ONLY. Entry is restricted to members of the ICT, Audio Visual and Entertainment industries.<br><br>Persons not in these categories, including children will not be admitted at any time.</div>
  <div class="abs follow" style="top:103px">Follow Us</div>
  <div class="abs follow-icons" style="top:121px"><span></span><span></span><span></span></div>
  <div class="abs partner"><small>in association with</small><div class="plate"></div></div>
</footer>
<div class="abs copyright">© 2011 Merriden Exhibitions, Australia. All rights reserved. Mezzanine level, 118 Larkin Street, Sydney, NSW 2000, Australia.</div>
<div class="abs organiser">merriden<i></i></div>
</body>
</html>
```